Law Firm Header Revision

Task: Redesign my law firm Word document header (modern, succinct, logo-first, easy address updates)

I need you to revise and modernize my Microsoft Word document header for Law Office of Bram Holcott, PLLC. The result should look professional and clean on letters (including Letters of Protection), with the logo as the main focus and the text kept succinct.

Goals:
1. Create a modern, minimal header that feels premium and uncluttered.
Make the logo the most visually dominant element.
Reduce the visual weight of the contact/address block so it doesn’t distract from the document.
Make the address easy to change later (I’m moving offices soon) while keeping the same header design.

2. Content to include (keep all info accurate):
Law Office of Bram Holcott, PLLC
615 Pemberly St. Ste #300-214, Houston, TX 77002
Office: 832.555.0143
Direct: 713.555.0187
Fax: 832.555.0129
Bholcottlaw.com

3. Layout requirements:
Provide 3 header style options:
Logo left + contact info right
Centered logo + single concise contact line below
Logo left + firm name prominent + minimal contact line
The primary line near the logo should be minimal (preferably website + main office phone).
The address should be easy to update in one place without redesigning the header. Prefer either:
Move the full address to the footer, or
Put the address in a single dedicated line/block so I can edit it once and keep the layout unchanged.
4. Build constraints:
Must be achievable using standard Microsoft Word tools only (header/footer, tables, alignment, fonts, spacing). No advanced graphics software.
Provide exact header text, plus step-by-step Word instructions for each option:
Font recommendations + sizes
Alignment
Spacing
Table setup (if used)
How to keep it consistent across pages

5. Deliverable:
For each of the 3 options, provide:
The exact header content (with line breaks)
Formatting specs (fonts, sizes, spacing)
Word build steps so I can recreate it reliably and keep the logo as the focal point.

```html
<!DOCTYPE html>
<html lang="en">
<head>
<meta charset="utf-8">
<title>Bram Holcott Law – Letterhead Options</title>
<link href="https://fonts.googleapis.com/css2?family=Roboto:wght@400;500;700&display=swap" rel="stylesheet">
<style>
  :root{
    --backdrop:#8e8e8e;
    --paper:#ffffff;
    --navy:#121a2c;
    --ink:#1d2433;
    --mark-faint:#eef0f4;
    --rule-light:#ffffff;
  }
  *{margin:0;padding:0;box-sizing:border-box}
  html,body{width:1200px;height:4012px;overflow:hidden}
  body{background:var(--backdrop);font-family:"Roboto",Arial,sans-serif;color:var(--ink);position:relative}
  .sheet{position:absolute;left:120px;width:960px;height:1250px;background:var(--paper);overflow:hidden}
  .sheet--one{top:140px}
  .sheet--two{top:1414px}
  .sheet--three{top:2688px}
  .shape{position:absolute;left:0;top:0}
  .brand{position:absolute;display:flex;align-items:center;gap:14px}
  .brand__square{width:54px;height:54px;background:var(--navy)}
  .brand__name{font-weight:500;font-size:34px;letter-spacing:1px;color:var(--navy);text-transform:uppercase}
  .brand--left{left:34px;top:32px}
  .brand--center{left:0;right:0;top:86px;justify-content:center}
  .firm-name{position:absolute;left:34px;top:110px;font-size:19px;font-weight:700;color:var(--navy)}
  .watermark{position:absolute;left:230px;top:330px;width:500px;height:500px;background:var(--mark-faint)}
  .contact{display:flex;align-items:center;gap:10px;font-size:13px;line-height:1.35}
  .icon{width:24px;height:24px;flex:none}
  .bar-contacts{position:absolute;top:13px;display:flex;gap:56px;color:#fff}
  .bar-contacts .icon rect{fill:none;stroke:#fff;stroke-width:1.2}
  .bar-contacts .icon path,.bar-contacts .icon circle.g{stroke:#fff}
  .line-contacts{position:absolute;left:0;right:0;top:176px;display:flex;justify-content:center;gap:60px}
  .footer-contacts{position:absolute;left:100px;top:1148px;display:flex;gap:90px;align-items:center}
  .footer-bar{position:absolute;left:0;bottom:0;width:960px;height:40px}
  .footer-label{position:absolute;bottom:9px;font-size:10px;color:#fff;letter-spacing:.5px}
  .footer-label--left{left:26px}
  .footer-label--right{right:30px}
</style>
</head>
<body>

<svg width="0" height="0" style="position:absolute">
  <defs>
    <symbol id="i-phone" viewBox="0 0 24 24"><rect x="0" y="0" width="24" height="24" rx="3" fill="var(--navy)"/><path d="M8 6l2.5 0 1 3-1.6 1.2a8 8 0 0 0 3.9 3.9L15 12.5l3 1 0 2.5c0 .8-.7 1.5-1.5 1.5A10.5 10.5 0 0 1 6.5 7.5C6.5 6.7 7.2 6 8 6z" fill="#fff"/></symbol>
    <symbol id="i-globe" viewBox="0 0 24 24"><rect x="0" y="0" width="24" height="24" rx="3" fill="var(--navy)"/><circle cx="12" cy="12" r="6" fill="none" stroke="#fff" stroke-width="1.3"/><path d="M6 12h12M12 6c-2.5 3-2.5 9 0 12M12 6c2.5 3 2.5 9 0 12" fill="none" stroke="#fff" stroke-width="1.1"/></symbol>
    <symbol id="i-pin" viewBox="0 0 24 24"><rect x="0" y="0" width="24" height="24" rx="3" fill="var(--navy)"/><path d="M12 5a4.5 4.5 0 0 1 4.5 4.5c0 3.3-4.5 8.5-4.5 8.5S7.5 12.8 7.5 9.5A4.5 4.5 0 0 1 12 5z" fill="#fff"/><circle cx="12" cy="9.5" r="1.7" fill="var(--navy)"/></symbol>
    <symbol id="i-fax" viewBox="0 0 24 24"><rect x="0" y="0" width="24" height="24" rx="3" fill="var(--navy)"/><rect x="8.5" y="5.5" width="7" height="4" fill="#fff"/><rect x="6" y="10" width="12" height="6" rx="1" fill="#fff"/><rect x="8.5" y="14.5" width="7" height="4" fill="#fff" stroke="var(--navy)" stroke-width=".8"/></symbol>
  </defs>
</svg>

<!-- Option 1: logo left, contacts in the top bar -->
<section class="sheet sheet--one">
  <svg class="shape" width="960" height="60" aria-hidden="true">
    <polygon points="470,0 960,0 960,54 516,54" fill="var(--navy)"/>
  </svg>
  <div class="brand brand--left"><span class="brand__square"></span><span class="brand__name">Bram Holcott</span></div>
  <div class="bar-contacts" style="left:560px">
    <div class="contact"><svg class="icon"><use href="#i-phone"/></svg>Office: 832.555.0143</div>
    <div class="contact"><svg class="icon"><use href="#i-globe"/></svg>Bholcottlaw.com</div>
  </div>
  <div class="watermark" role="img" aria-label="Faint brand square behind the letter body"></div>
  <div class="footer-contacts">
    <div class="contact"><svg class="icon"><use href="#i-pin"/></svg><span>615 Pemberly St. Ste #300-214,<br>Houston, TX 77002</span></div>
    <div class="contact"><svg class="icon"><use href="#i-fax"/></svg>Fax: 832.555.0129</div>
    <div class="contact"><svg class="icon"><use href="#i-phone"/></svg>Direct: 713.555.0187</div>
  </div>
  <svg class="footer-bar" viewBox="0 0 960 40" aria-hidden="true">
    <polygon points="0,14 780,14 800,0 960,0 960,40 0,40" fill="var(--navy)"/>
    <line x1="770" y1="40" x2="812" y2="6" stroke="#fff" stroke-width="2"/>
  </svg>
  <span class="footer-label footer-label--left">LETTER PROTECTION</span>
  <span class="footer-label footer-label--right">01</span>
</section>

<!-- Option 2: centered logo, single contact line -->
<section class="sheet sheet--two">
  <svg class="shape" width="960" height="60" aria-hidden="true">
    <rect x="0" y="0" width="960" height="8" fill="var(--navy)"/>
    <polygon points="0,0 330,0 296,48 0,48" fill="var(--navy)"/>
    <line x1="308" y1="48" x2="344" y2="0" stroke="var(--navy)" stroke-width="3"/>
    <polygon points="630,0 960,0 960,48 664,48" fill="var(--navy)"/>
    <line x1="616" y1="0" x2="652" y2="48" stroke="var(--navy)" stroke-width="3"/>
    <line x1="344" y1="2" x2="616" y2="2" stroke="var(--navy)" stroke-width="4"/>
  </svg>
  <div class="brand brand--center"><span class="brand__square"></span><span class="brand__name">Bram Holcott</span></div>
  <div class="line-contacts">
    <div class="contact"><svg class="icon"><use href="#i-phone"/></svg>Office: 832.555.0143</div>
    <div class="contact"><svg class="icon"><use href="#i-globe"/></svg>Bholcottlaw.com</div>
  </div>
  <div class="watermark" role="img" aria-label="Faint brand square behind the letter body" style="top:360px"></div>
  <div class="footer-contacts">
    <div class="contact"><svg class="icon"><use href="#i-pin"/></svg><span>615 Pemberly St. Ste #300-214,<br>Houston, TX 77002</span></div>
    <div class="contact"><svg class="icon"><use href="#i-fax"/></svg>Fax: 832.555.0129</div>
    <div class="contact"><svg class="icon"><use href="#i-phone"/></svg>Direct: 713.555.0187</div>
  </div>
  <svg class="footer-bar" viewBox="0 0 960 40" aria-hidden="true">
    <polygon points="0,14 780,14 800,0 960,0 960,40 0,40" fill="var(--navy)"/>
    <line x1="770" y1="40" x2="812" y2="6" stroke="#fff" stroke-width="2"/>
  </svg>
  <span class="footer-label footer-label--left">LETTER PROTECTION</span>
  <span class="footer-label footer-label--right">01</span>
</section>

<!-- Option 3: logo left, firm name prominent -->
<section class="sheet sheet--three">
  <svg class="shape" width="960" height="80" aria-hidden="true">
    <polygon points="420,0 960,0 960,70 472,70" fill="var(--navy)"/>
    <line x1="390" y1="0" x2="444" y2="70" stroke="var(--navy)" stroke-width="3"/>
    <line x1="460" y1="0" x2="512" y2="70" stroke="var(--rule-light)" stroke-width="2"/>
  </svg>
  <div class="brand brand--left"><span class="brand__square"></span><span class="brand__name">Bram Holcott</span></div>
  <p class="firm-name">Law Office of Bram Holcott, PLLC</p>
  <div class="bar-contacts" style="left:570px;top:22px">
    <div class="contact"><svg class="icon"><use href="#i-phone"/></svg>Office: 832.555.0143</div>
    <div class="contact"><svg class="icon"><use href="#i-globe"/></svg>Bholcottlaw.com</div>
  </div>
  <div class="watermark" role="img" aria-label="Faint brand square behind the letter body" style="top:380px"></div>
  <div class="footer-contacts">
    <div class="contact"><svg class="icon"><use href="#i-pin"/></svg><span>615 Pemberly St. Ste #300-214,<br>Houston, TX 77002</span></div>
    <div class="contact"><svg class="icon"><use href="#i-fax"/></svg>Fax: 832.555.0129</div>
    <div class="contact"><svg class="icon"><use href="#i-phone"/></svg>Direct: 713.555.0187</div>
  </div>
  <svg class="footer-bar" viewBox="0 0 960 40" aria-hidden="true">
    <polygon points="0,14 780,14 800,0 960,0 960,40 0,40" fill="var(--navy)"/>
    <line x1="770" y1="40" x2="812" y2="6" stroke="#fff" stroke-width="2"/>
  </svg>
  <span class="footer-label footer-label--left">LETTER PROTECTION</span>
  <span class="footer-label footer-label--right">01</span>
</section>

</body>
</html>
```